Looking for someone to design a business card for my plumbing business Quandor Plumbing Solutions I want the background also to be black, must attract clients. If possible I want the front to be the logo and the back to show maybe the details.

Target Market(s)

Clients

Industry/Entity Type

Plumbing maintenance

Contact Information for Business Card

Name: Felix, Contact: 0461 539 207, Email: quandorplumbingsolutions@mailbrook.example, Licence number 728093K

Font styles to use
Other font styles liked:
• as per logo maybe?

Colors

Designer to choose colors to be used in the design.

Requirements
Nice to have
• stating the service I provide, emergency plumbing, plumbing maintenance, drainage maintenance, block sewer and stormwater, camera and locating.

```html
<!DOCTYPE html>
<html lang="en">
<head>
<meta charset="utf-8">
<title>Quandor Plumbing Solutions – Business Card</title>
<link rel="stylesheet" href="https://fonts.googleapis.com/css2?family=Figtree:wght@400;500;700;800&display=swap">
<style>
  :root {
    --page-bg: #161616;
    --card-bg: #222222;
    --brand-blue: #4a8fd0;
    --text-light: #f2f2f2;
    --band-white: #f4f4f4;
  }
  * { margin: 0; padding: 0; box-sizing: border-box; }
  html, body {
    width: 1200px; height: 1059px; overflow: hidden;
    background: var(--page-bg);
    font-family: "Figtree", sans-serif;
    color: var(--text-light);
  }
  .card {
    position: absolute; left: 255px;
    width: 690px; height: 392px;
    background: var(--card-bg);
    border-radius: 18px;
    overflow: hidden;
  }
  .card--details { top: 89px; }
  .card--brand { top: 547px; }

  .brand-name {
    position: absolute;
    font-weight: 800;
    color: var(--text-light);
    text-transform: uppercase;
    line-height: 1.05;
    white-space: nowrap;
  }
  .card--details .brand-name {
    right: 39px; top: 98px;
    font-size: 28px; text-align: right;
  }
  .card--brand .brand-name {
    left: 0; right: 0; top: 150px;
    font-size: 42px; text-align: center;
  }

  .person { position: absolute; left: 35px; top: 171px; }
  .person__name {
    font-size: 30px; font-weight: 800; color: var(--brand-blue);
    text-transform: uppercase; letter-spacing: 0.5px; line-height: 1;
  }
  .person__role { font-size: 15.5px; margin-top: 4px; }

  .divider {
    position: absolute; left: 35px; right: 39px; top: 234px;
    height: 2px; background: var(--brand-blue);
  }

  .contact {
    position: absolute; left: 35px; top: 251px; width: 380px;
    list-style: none; font-size: 15.5px; white-space: nowrap;
  }
  .contact li { display: flex; align-items: center; height: 27.5px; }
  .contact li.licence { height: 22px; margin-bottom: 10px; }
  .contact svg { width: 13px; height: 13px; margin-right: 7px; flex: none; }

  .services {
    position: absolute; right: 36px; top: 251px;
    list-style: none; font-size: 15.5px; text-align: right; white-space: nowrap;
  }
  .services li { height: 22px; line-height: 22px; }
  .services li::after {
    content: ""; display: inline-block;
    width: 5px; height: 5px; border-radius: 50%;
    background: var(--brand-blue); margin-left: 7px; vertical-align: 3px;
  }

  .base-band { position: absolute; left: 0; bottom: 0; width: 690px; height: 14px; }
</style>
</head>
<body>

<section class="card card--details" aria-label="Business card, details side">
  <div class="brand-name">Quandor<br>Plumbing Solutions</div>

  <div class="person">
    <div class="person__name">Felix</div>
    <div class="person__role">Founder &amp; CEO</div>
  </div>

  <div class="divider"></div>

  <ul class="contact">
    <li class="licence">Licence number 728093K</li>
    <li>
      <svg viewBox="0 0 16 16" aria-hidden="true"><path fill="#4a8fd0" d="M3.6 1.2l2.3 2.6-1.3 1.9c.9 2 2.5 3.6 4.6 4.6l1.9-1.3 2.6 2.3-1.4 2.3C7.2 13.9 2 8.8 1.4 2.6z"/></svg>
      0461 539 207
    </li>
    <li>
      <svg viewBox="0 0 16 16" aria-hidden="true"><rect x="1" y="3" width="14" height="10" fill="#4a8fd0"/><path d="M1 3l7 6 7-6" fill="none" stroke="#222" stroke-width="1.4"/></svg>
      quandorplumbingsolutions@mailbrook.example
    </li>
    <li>
      <svg viewBox="0 0 16 16" aria-hidden="true"><circle cx="8" cy="8" r="7" fill="#4a8fd0"/></svg>
      @QuandorPlumbingSolutions
    </li>
  </ul>

  <ul class="services">
    <li>Emergency plumbing</li>
    <li>Plumbing maintenance</li>
    <li>Drainage maintenance</li>
    <li>Block sewer and stormwater</li>
    <li>Camera and locating</li>
  </ul>

  <svg class="base-band" viewBox="0 0 690 14" preserveAspectRatio="none" aria-hidden="true">
    <polygon points="0,0 349,0 335,14 0,14" fill="#4a8fd0"/>
    <polygon points="358,0 690,0 690,14 344,14" fill="#f4f4f4"/>
  </svg>
</section>

<section class="card card--brand" aria-label="Business card, brand side">
  <div class="brand-name">Quandor<br>Plumbing Solutions</div>
</section>

</body>
</html>
```